KORV PTY LTD - Business Cards

Design a modern business card - using the attached Designs.
Same design as on the front, apart from the names/numbers/emails to be different.
We want the cards to be very glossy to stand out, do I think the simple black/white/metallic will be effective.
Both lots of details below:

Tom Wrenshaw
Director
tom_korv@nulvane.com
0438 274 093

Lewis Corbyn
Director
lewis_korv@nulvane.com
0419 385 642

Industry/Entity Type

Business

```html
<!DOCTYPE html>
<html lang="en">
<head>
<meta charset="utf-8">
<title>KORV PTY LTD – Business Cards</title>
<link href="https://fonts.googleapis.com/css2?family=Rajdhani:wght@500;600&display=swap" rel="stylesheet">
<style>
  :root {
    --backdrop: #8d8d8f;
    --card: #f4f4f4;
    --card-edge: #e2e2e2;
    --ink: #34383b;
    --panel: #3a3e41;
    --panel-text: #eef0f1;
    --rule: #9a9c9e;
    --soft: #5a5e61;
  }
  * { box-sizing: border-box; margin: 0; padding: 0; }
  html, body { width: 1200px; height: 933px; overflow: hidden; }
  body {
    background: var(--backdrop);
    font-family: "Rajdhani", "Arial Narrow", sans-serif;
    position: relative;
  }
  .card {
    position: absolute;
    width: 540px;
    height: 308px;
    background: linear-gradient(135deg, #ffffff 0%, var(--card) 55%, var(--card-edge) 100%);
    box-shadow: 0 6px 18px rgba(0,0,0,0.25);
    overflow: hidden;
  }
  .card--back { left: 330px; top: 133px; }
  .card--tom { left: 40px; top: 491px; }
  .card--lewis { left: 620px; top: 491px; }

  /* back */
  .back-block {
    position: absolute;
    left: 72px; top: 0;
    width: 146px; height: 142px;
    background: var(--panel);
  }

  /* brand lockup */
  .brand {
    position: absolute;
    display: flex;
    align-items: center;
    gap: 9px;
  }
  .brand__dot {
    width: 22px; height: 22px;
    border-radius: 50%;
    background: var(--panel);
  }
  .brand__name {
    font-weight: 600;
    font-size: 22px;
    letter-spacing: 0.8px;
    color: var(--ink);
    white-space: nowrap;
  }
  .card--back .brand { left: 330px; top: 136px; }
  .card--front .brand { left: 345px; top: 84px; }

  /* front */
  .contact-panel {
    position: absolute;
    left: 45px; top: 44px;
    width: 165px; height: 159px;
    background: var(--panel);
    color: var(--panel-text);
    padding: 15px 10px 0 13px;
  }
  .contact-panel__address {
    font-weight: 500;
    font-size: 11px;
    line-height: 15px;
    margin-bottom: 9px;
  }
  .contact-list { list-style: none; }
  .contact-list li {
    display: flex;
    align-items: center;
    gap: 6px;
    font-weight: 500;
    font-size: 10px;
    line-height: 17px;
    white-space: nowrap;
  }
  .contact-list svg { width: 9px; height: 9px; flex: none; fill: var(--panel-text); }

  .rule {
    position: absolute;
    background: var(--rule);
    height: 2px;
  }
  .rule--top { left: 225px; right: 0; top: 147px; }
  .rule--bottom { left: 345px; right: 0; top: 207px; }

  .person {
    position: absolute;
    left: 228px; top: 154px;
    color: var(--ink);
  }
  .person__name {
    font-weight: 600;
    font-size: 30px;
    line-height: 32px;
    letter-spacing: 0.4px;
    white-space: nowrap;
  }
  .person__role {
    font-weight: 500;
    font-size: 13px;
    letter-spacing: 1.2px;
    color: var(--soft);
  }
</style>
</head>
<body>

  <section class="card card--back" aria-label="Card back">
    <div class="back-block"></div>
    <div class="brand">
      <span class="brand__dot"></span>
      <span class="brand__name">KORV PTY LTD</span>
    </div>
  </section>

  <section class="card card--front card--tom" aria-label="Card front, Tom Wrenshaw">
    <div class="contact-panel">
      <p class="contact-panel__address">27 Harlow Ridge Road<br>Unit 4, Ferncliff Street</p>
      <ul class="contact-list">
        <li>
          <svg viewBox="0 0 12 12"><path d="M3 1h2l1 3-1.5 1a6 6 0 0 0 2.5 2.5L8 6l3 1v2a1 1 0 0 1-1 1A9 9 0 0 1 2 2a1 1 0 0 1 1-1z"/></svg>
          0438 274 093
        </li>
        <li>
          <svg viewBox="0 0 12 12"><path d="M3.5 0h5a1 1 0 0 1 1 1v10a1 1 0 0 1-1 1h-5a1 1 0 0 1-1-1V1a1 1 0 0 1 1-1zM4 1.5v8h4v-8z"/></svg>
          0438 274 093
        </li>
        <li>
          <svg viewBox="0 0 12 12"><path d="M0 2h12v8H0zM1 3v.4l5 3.2 5-3.2V3z"/></svg>
          tom_korv@nulvane.com
        </li>
        <li>
          <svg viewBox="0 0 12 12"><path d="M6 0a6 6 0 1 0 0 12A6 6 0 0 0 6 0zm0 1.2c.7.8 1.2 2.4 1.3 4.2H4.7C4.8 3.6 5.3 2 6 1.2zM1.3 6.6h2.3c.1 1.5.4 2.8 1 3.8a4.8 4.8 0 0 1-3.3-3.8zm0-1.2a4.8 4.8 0 0 1 3.3-3.8c-.6 1-.9 2.3-1 3.8zm3.4 1.2h2.6c-.1 1.8-.6 3.4-1.3 4.2-.7-.8-1.2-2.4-1.3-4.2zm3.7 0h2.3a4.8 4.8 0 0 1-3.3 3.8c.6-1 .9-2.3 1-3.8zm0-1.2c-.1-1.5-.4-2.8-1-3.8a4.8 4.8 0 0 1 3.3 3.8z"/></svg>
          www.korvpty.com.au
        </li>
      </ul>
    </div>
    <div class="brand">
      <span class="brand__dot"></span>
      <span class="brand__name">KORV PTY LTD</span>
    </div>
    <div class="rule rule--top"></div>
    <div class="person">
      <p class="person__name">TOM WRENSHAW</p>
      <p class="person__role">DIRECTOR</p>
    </div>
    <div class="rule rule--bottom"></div>
  </section>

  <section class="card card--front card--lewis" aria-label="Card front, Lewis Corbyn">
    <div class="contact-panel">
      <p class="contact-panel__address">27 Harlow Ridge Road<br>Unit 4, Ferncliff Street</p>
      <ul class="contact-list">
        <li>
          <svg viewBox="0 0 12 12"><path d="M3 1h2l1 3-1.5 1a6 6 0 0 0 2.5 2.5L8 6l3 1v2a1 1 0 0 1-1 1A9 9 0 0 1 2 2a1 1 0 0 1 1-1z"/></svg>
          0419 385 642
        </li>
        <li>
          <svg viewBox="0 0 12 12"><path d="M3.5 0h5a1 1 0 0 1 1 1v10a1 1 0 0 1-1 1h-5a1 1 0 0 1-1-1V1a1 1 0 0 1 1-1zM4 1.5v8h4v-8z"/></svg>
          0419 385 642
        </li>
        <li>
          <svg viewBox="0 0 12 12"><path d="M0 2h12v8H0zM1 3v.4l5 3.2 5-3.2V3z"/></svg>
          lewis_korv@nulvane.com
        </li>
        <li>
          <svg viewBox="0 0 12 12"><path d="M6 0a6 6 0 1 0 0 12A6 6 0 0 0 6 0zm0 1.2c.7.8 1.2 2.4 1.3 4.2H4.7C4.8 3.6 5.3 2 6 1.2zM1.3 6.6h2.3c.1 1.5.4 2.8 1 3.8a4.8 4.8 0 0 1-3.3-3.8zm0-1.2a4.8 4.8 0 0 1 3.3-3.8c-.6 1-.9 2.3-1 3.8zm3.4 1.2h2.6c-.1 1.8-.6 3.4-1.3 4.2-.7-.8-1.2-2.4-1.3-4.2zm3.7 0h2.3a4.8 4.8 0 0 1-3.3 3.8c.6-1 .9-2.3 1-3.8zm0-1.2c-.1-1.5-.4-2.8-1-3.8a4.8 4.8 0 0 1 3.3 3.8z"/></svg>
          www.korvpty.com.au
        </li>
      </ul>
    </div>
    <div class="brand">
      <span class="brand__dot"></span>
      <span class="brand__name">KORV PTY LTD</span>
    </div>
    <div class="rule rule--top"></div>
    <div class="person">
      <p class="person__name">LEWIS CORBYN</p>
      <p class="person__role">DIRECTOR</p>
    </div>
    <div class="rule rule--bottom"></div>
  </section>

</body>
</html>
```